ZESTORAMA Business Card Design

ZESTORAMA
Zestorama is a food van, serving high vibe delicious food to go. This business is dedicated to healthy delicious feel good food, beauty in service and a sustainable planet.

The van will operate in the south west of western Australia at music festivals events markets wherever people need great food to go!

I like the idea of vibrant green mixed with a yellow?? background with some rays like the sun through the background.
The font needs to say vibrant energetic
TO ME -vibrant energetic font has to appear to be on the move - perhaps with shading??

I like fusha if that works for font? but the colour has to say food too.

I would like a symbol on the card a simple V turned into a womans raised arms. This should be vibrant too.
Thank you
Blessings
Marisol

Target Market(s)

target lovers of healthy high vibe food. music festival goers. age 18- 50 feel. audiance conscious eaters of feel great food

Industry/Entity Type

Events

Contact Information for Business Card

ZESTORAMA
High Vibe Food
Van
Marisol -owner/opperator
0471583906
Face book symbol - ZESTORAMA

on the I would like a logo of a simple V turned into a womans arms up toward the sky flip side

My number and name again
Zestorama- feel great mobile food
Festivals, events, markets & where high vibe food 2 go is appreciated

Requirements
Nice to have
• Moving energetic font
colour that says high vibe and healthy food

a logo that is a simple V turned into a woman's raised arms in gratitude

```html
<!DOCTYPE html>
<html lang="en">
<head>
<meta charset="utf-8">
<title>Zestorama Business Card</title>
<link rel="stylesheet" href="https://fonts.googleapis.com/css2?family=Mulish:wght@700;900&display=swap">
<style>
  :root {
    --page-bg: #5e4e42;
    --lime: #b9e21f;
    --yellow: #e6ef3a;
    --green: #5fb82a;
    --fuchsia: #e8287e;
    --fuchsia-deep: #b5145e;
    --ink: #2a1430;
    --white: #ffffff;
  }
  * { box-sizing: border-box; margin: 0; padding: 0; }
  html, body { width: 1200px; height: 723px; overflow: hidden; }
  body {
    background: var(--page-bg);
    font-family: "Mulish", "Century Gothic", sans-serif;
    display: flex;
    align-items: center;
    justify-content: center;
    gap: 60px;
  }
  .card {
    position: relative;
    width: 360px;
    height: 630px;
    border-radius: 6px;
    overflow: hidden;
    box-shadow: 0 12px 30px rgba(0,0,0,.35);
  }
  .card__rays {
    position: absolute;
    inset: 0;
    background:
      radial-gradient(circle at 50% 30%, var(--yellow) 0%, var(--lime) 45%, var(--green) 100%);
  }
  .card__content {
    position: relative;
    height: 100%;
    display: flex;
    flex-direction: column;
    align-items: center;
    text-align: center;
  }

  /* Front */
  .front .card__content { padding: 40px 24px 36px; }
  .mark-circle {
    width: 150px;
    height: 150px;
    border-radius: 50%;
    background: var(--fuchsia);
    border: 4px solid var(--ink);
  }
  .wordmark {
    margin-top: 22px;
    font-size: 44px;
    font-weight: 900;
    color: var(--fuchsia);
    letter-spacing: -1px;
  }
  .tagline {
    margin-top: 4px;
    font-size: 25px;
    font-weight: 900;
    color: var(--fuchsia);
    text-shadow: 2px 2px 0 var(--ink);
  }
  .owner { margin-top: 30px; }
  .owner__name { font-size: 26px; font-weight: 900; color: var(--fuchsia); }
  .owner__role { font-size: 24px; font-weight: 700; color: var(--fuchsia); }
  .owner__phone { margin-top: 6px; font-size: 28px; font-weight: 900; color: var(--fuchsia); }
  .social {
    margin-top: 34px;
    display: flex;
    flex-direction: column;
    align-items: center;
    gap: 6px;
  }
  .social__square {
    width: 34px; height: 34px;
    border-radius: 5px;
    background: var(--fuchsia);
  }
  .social__name { font-size: 28px; font-weight: 900; color: var(--fuchsia); }
  .email {
    margin-top: auto;
    font-size: 19px;
    font-weight: 700;
    color: var(--fuchsia-deep);
  }

  /* Back */
  .back .card__content { padding: 34px 22px 30px; }
  .back__name { font-size: 42px; font-weight: 900; color: var(--fuchsia); letter-spacing: -1px; }
  .back__intro {
    margin-top: 6px;
    font-size: 19px;
    font-weight: 900;
    line-height: 1.2;
    color: var(--fuchsia);
    text-shadow: 1.5px 1.5px 0 var(--ink);
  }
  .back .mark-circle { margin-top: 22px; width: 120px; height: 120px; }
  .back__body {
    margin-top: 20px;
    font-size: 19px;
    font-weight: 900;
    line-height: 1.25;
    color: var(--fuchsia);
    text-shadow: 1.5px 1.5px 0 var(--ink);
  }
  .back__cta { margin-top: auto; font-size: 22px; }
</style>
</head>
<body>
  <article class="card front">
    <div class="card__rays" role="img" aria-label="Sunburst rays in lime, yellow and green"></div>
    <div class="card__content">
      <div class="mark-circle"></div>
      <h1 class="wordmark">ZESTORAMA</h1>
      <p class="tagline">High Vibe Food Van</p>
      <div class="owner">
        <p class="owner__name">Marisol</p>
        <p class="owner__role">owner/operator</p>
        <p class="owner__phone">0471583906</p>
      </div>
      <div class="social">
        <span class="social__square"></span>
        <span class="social__name">ZESTORAMA</span>
      </div>
      <p class="email">marisol@zestorama.com</p>
    </div>
  </article>

  <article class="card back">
    <div class="card__rays" role="img" aria-label="Sunburst rays in lime, yellow and green"></div>
    <div class="card__content">
      <h2 class="back__name">ZESTORAMA</h2>
      <p class="back__intro">Food That Makes You Feel Great at festivals, community events &amp; private gatherings</p>
      <div class="mark-circle"></div>
      <p class="back__body">Dedicated to conscious, joyous eating. VIBRANT breakfast bowls, coconuts &amp; DELICIOUS nourishing soups. ZESTORAMA includes vegetarians, vegans &amp; gluten free-ers!</p>
      <p class="back__body back__cta">Got The Vibe?</p>
    </div>
  </article>
</body>
</html>
```